Modern business card design for professional copywriter

I'd like a business card design that I can use to have my cards printed out by quillprint.com as a squared corners business card (see artwork and design guidelines here: https://help.quillprint.com/hc/en-gb/sections/200570950-QUILL-Product-Templates)

The design should be clean and modern and reflect the colours, tone and branding on my website: https://tessavorrin.com.au

Target Market(s)

Professionals, B2B small business owners

Industry/Entity Type

Business

Contact Information for Business Card

Tessa Vorrin
m: 0468 905 327
e: tessa@tessavorrin.com.au
w: tessavorrin.com.au

Font styles to use
Sans Serif

Requirements
Must have
• Tagline: "Smart copywriting for clever business people"
• Brand colours: fd8000, 009984, 666666 and black
Nice to have

```html
<!DOCTYPE html>
<html lang="en">
<head>
<meta charset="utf-8">
<title>Tessa Vorrin — Business Card</title>
<link href="https://fonts.googleapis.com/css2?family=Jost:wght@400;500&family=Oswald:wght@500&display=swap" rel="stylesheet">
<style>
  :root {
    --teal: #119b86;
    --orange: #fd8000;
    --grey: #666666;
    --paper: #ffffff;
    --backdrop: #ece9e3;
  }
  * { box-sizing: border-box; margin: 0; padding: 0; }
  html, body {
    width: 1200px;
    height: 929px;
    overflow: hidden;
    background: var(--backdrop);
  }
  .sheet {
    position: relative;
    width: 1200px;
    height: 929px;
  }
  .card {
    position: absolute;
    top: 296px;
    width: 520px;
    height: 336px;
    box-shadow: 0 6px 18px rgba(0, 0, 0, 0.18);
  }
  .card--front {
    left: 60px;
    background: var(--teal);
    display: flex;
    align-items: center;
    justify-content: center;
  }
  .brand-name {
    font-family: "Jost", sans-serif;
    font-weight: 500;
    font-size: 46px;
    letter-spacing: -0.5px;
    color: var(--paper);
  }
  .card--back {
    left: 620px;
    background: var(--paper);
  }
  .identity {
    position: absolute;
    left: 48px;
    top: 118px;
    display: flex;
    align-items: center;
  }
  .person-name {
    font-family: "Oswald", sans-serif;
    font-weight: 500;
    font-size: 36px;
    letter-spacing: 0.5px;
    color: var(--teal);
    line-height: 1;
  }
  .divider {
    width: 2px;
    height: 58px;
    background: var(--orange);
    margin: 0 18px 0 20px;
  }
  .contact-list {
    list-style: none;
    font-family: "Jost", sans-serif;
    font-size: 14px;
    color: var(--grey);
    line-height: 1.45;
  }
  .contact-list li {
    display: flex;
    align-items: center;
    gap: 8px;
  }
  .contact-list svg {
    width: 11px;
    height: 11px;
    flex: none;
  }
  .tagline {
    position: absolute;
    left: 0;
    right: 0;
    top: 236px;
    text-align: center;
    font-family: "Jost", sans-serif;
    font-size: 14px;
    letter-spacing: 0.6px;
    color: var(--grey);
  }
</style>
</head>
<body>
<main class="sheet">
  <section class="card card--front" aria-label="Card front">
    <span class="brand-name">Tessa Vorrin</span>
  </section>

  <section class="card card--back" aria-label="Card back">
    <div class="identity">
      <h1 class="person-name">TESSA VORRIN</h1>
      <span class="divider"></span>
      <ul class="contact-list">
        <li>
          <svg viewBox="0 0 12 12" aria-hidden="true"><rect x="3" y="0.8" width="6" height="10.4" rx="1" fill="none" stroke="#119b86" stroke-width="1.2"/><line x1="5" y1="9.4" x2="7" y2="9.4" stroke="#119b86" stroke-width="1"/></svg>
          0468 905 327
        </li>
        <li>
          <svg viewBox="0 0 12 12" aria-hidden="true"><rect x="0.5" y="2.5" width="11" height="7.5" fill="#119b86"/><polyline points="0.8,2.8 6,7 11.2,2.8" fill="none" stroke="#fff" stroke-width="1"/></svg>
          tessa@tessavorrin.com.au
        </li>
        <li>
          <svg viewBox="0 0 12 12" aria-hidden="true"><circle cx="5" cy="5" r="3.4" fill="none" stroke="#119b86" stroke-width="1.6"/><line x1="7.5" y1="7.5" x2="11" y2="11" stroke="#119b86" stroke-width="1.8"/></svg>
          tessavorrin.com.au
        </li>
      </ul>
    </div>
    <p class="tagline">Smart copywriting for clever business people</p>
  </section>
</main>
</body>
</html>
```